Moon Tot needs ecommerce website design help

We need someone to set up a fully functional website for us. We sell baby bibs, I attached them along with our company logo (MTG: moon tot goods). The bibs are made of 100% silicon, they are safe, light weight, soft, smooth, flexible, dishwasher safe and has funny faces.

Business name: Moon Tot Goods
Elm Hollow, NY 00000
email: MoonTotGoods@mailbox-example.com
tel.: (555) 014-TOTS
website: MoonTotGoods-example.com

Target Market(s)

18-40

Industry/Entity Type

Baby

Coding

Coded - Design and coding required

Number of Pages Required

5+ page

Requirements
Must have
• 1. Pages: Why buy from us, Contact Us, Home page, Products Page, Blog
• 2. Use the colors from our logo for the web design.
• 3. Need a link that will connect visitors to our facebook, instagram, Pinterest and Tumblr account. Would like links on,the top left side of the page
Nice to have
• My Cart page
• 1. On contact us page, we want to include some type of template for the customer to complete. (Ex: name, email address, contact number, optional home address, comments)
• 2. When clients visit our website, we want a capture/pop up for the customer to subscribe to our email list to receive discounts. (Ex. Want 10% off your next order ? Suscribe to our mailing list below and get a 10% off code to use at check out. If they don't want to subscribe, they have the option to select "No Thank You, I want to pay full price).
• 3. On home page have subscribe to our email list.

```html
<!DOCTYPE html>
<html lang="en">
<head>
<meta charset="utf-8">
<title>Moon Tot Goods – Baby Bibs</title>
<link href="https://fonts.googleapis.com/css2?family=Raleway:wght@400;500;600;700&display=swap" rel="stylesheet">
<style>
:root{
  --pink:#f0475b;
  --green:#8dc21f;
  --orange:#fbb75c;
  --text:#444;
  --muted:#666;
  --panel:#f3f3f3;
  --border:#e2e2e2;
  --footer:#555;
  --footer-bar:#4a4a4a;
  --white:#fff;
}
*{box-sizing:border-box;margin:0;padding:0}
html,body{width:737px;height:1200px;overflow:hidden}
body{font-family:"Raleway",sans-serif;color:var(--text);background:var(--white);position:relative}
.abs{position:absolute}
a{color:inherit;text-decoration:none}

/* header */
.brand{left:46px;top:18px;display:flex;align-items:center;gap:8px}
.brand-dot{width:30px;height:30px;border-radius:50%;background:var(--green)}
.brand-name{font-size:26px;font-weight:700;color:var(--pink);letter-spacing:1px}
.top-links{right:46px;top:14px;font-size:8.5px;color:var(--muted)}
.top-links span{margin:0 4px;color:#aaa}
.nav{left:211px;top:50px;display:flex;gap:21px;font-size:8px;font-weight:600;color:#444}
.nav .active{color:var(--pink)}
.cart{left:572px;top:50px;font-size:8px;font-weight:700;color:var(--green);display:flex;gap:5px;align-items:center}
.cart b{color:#333}
.search{left:683px;top:50px}

/* hero */
.hero{left:0;top:70px;width:737px;height:283px;background:linear-gradient(90deg,#c98a3a 0%,#d9a458 35%,#b98542 60%,#8c6a4a 100%)}
.hero-photo{left:312px;top:70px;width:425px;height:283px;background:radial-gradient(circle at 70% 40%,#6b4a3a 0%,#8a6a52 35%,#5c8fc4 70%,#c39654 100%);opacity:.85}
.hero-title{left:46px;top:147px;font-size:26px;font-weight:700;color:var(--white);letter-spacing:.5px}
.hero-sub{left:46px;top:184px;width:245px;font-size:10px;font-weight:600;line-height:16px;color:var(--white)}
.btn{display:inline-flex;align-items:center;justify-content:center;background:var(--pink);color:var(--white);font-weight:700}
.shop{left:46px;top:230px;width:101px;height:30px;font-size:10px}
.dots{left:46px;top:287px;display:flex;gap:5px}
.dots i{width:7px;height:7px;background:var(--white);border-radius:1px}
.dots i:first-child{background:var(--green)}

/* featured */
.section-title{left:0;width:737px;top:380px;text-align:center;font-size:13px;font-weight:500;color:#333;letter-spacing:.5px}
.card{top:411px;width:148px;height:218px;border:2px solid var(--border);background:var(--white);text-align:center}
.card-img{margin:8px auto 0;width:90px;height:100px;border-radius:40% 40% 45% 45%}
.card-name{margin-top:14px;font-size:11.5px;font-weight:500;color:var(--pink)}
.card-desc{margin-top:4px;font-size:9px;line-height:14px;color:var(--muted);padding:0 16px}
.card-price{margin-top:8px;font-size:11px;font-weight:600;color:#333}
.cart-btn{top:614px;width:32px;height:32px;border-radius:50%;background:var(--green);display:flex;align-items:center;justify-content:center}
.divider{left:46px;top:673px;width:645px;height:1px;background:var(--border)}

/* info panels */
.welcome{left:46px;top:698px;width:203px;height:180px;background:var(--orange);padding:17px 15px}
.panel-title{font-size:13.5px;font-weight:500;color:var(--white);letter-spacing:.5px}
.welcome p{margin-top:8px;font-size:8.8px;line-height:16px;color:#fdf1dd}
.small-btn{height:22px;padding:0 10px;font-size:8px}
.welcome .small-btn{position:absolute;left:14px;top:144px}
.why{left:266px;top:698px;width:424px;height:180px;background:var(--panel);padding:17px 19px}
.why .panel-title{color:#333}
.why p{margin-top:8px;width:315px;font-size:8.8px;line-height:16px;color:var(--muted);white-space:nowrap}
.features{position:absolute;left:19px;top:78px;display:grid;grid-template-columns:123px 110px;row-gap:8px;font-size:8.8px;color:var(--green);font-weight:500}
.features span{display:flex;align-items:center;gap:8px}
.why .small-btn{position:absolute;left:19px;top:144px}
.why-img{left:598px;top:738px;width:70px;height:104px;border-radius:40% 40% 45% 45%;background:linear-gradient(#e0359a,#c21e7c)}

/* blog & newsletter */
.blog{left:46px;top:891px;width:424px;height:125px;background:var(--panel);padding:16px 15px}
.blog .panel-title{color:#333}
.blog-arrows{position:absolute;right:20px;top:18px}
.blog h3{margin-top:9px;font-size:11px;font-weight:500;color:var(--pink)}
.blog p{margin-top:3px;font-size:9px;line-height:16px;color:var(--muted)}
.blog small{display:block;margin-top:8px;font-size:7.5px;font-weight:700;color:var(--green)}
.news{left:489px;top:891px;width:202px;height:125px;background:var(--orange);padding:16px 15px}
.news p{margin-top:6px;font-size:8.8px;line-height:14px;color:#fdf1dd}
.news-form{position:absolute;left:15px;top:78px;display:flex}
.news-input{width:144px;height:28px;background:var(--white);font-size:9px;color:var(--muted);padding:0 8px;display:flex;align-items:center}
.news-go{width:29px;height:28px;background:var(--green);color:var(--white);font-size:10px;font-weight:700;display:flex;align-items:center;justify-content:center}

/* footer */
.footer{left:0;top:1043px;width:737px;height:122px;background:var(--footer)}
.foot-brand{left:46px;top:1066px;display:flex;align-items:center;gap:7px}
.foot-brand .brand-name{font-size:22px}
.foot-brand .brand-dot{width:24px;height:24px}
.foot-about{left:46px;top:1106px;width:190px;font-size:8.3px;line-height:14.5px;color:#ddd}
.foot-col{top:1064px;font-size:8.3px;line-height:15.2px;color:#ddd}
.foot-col h4{font-size:8.5px;font-weight:700;color:var(--orange);margin-bottom:2px;letter-spacing:.3px}
.foot-col strong{color:var(--white);font-weight:700}
.contact-row{display:flex;align-items:center;gap:8px;margin-top:4px}
.foot-bar{left:0;top:1165px;width:737px;height:35px;background:var(--footer-bar)}
.copyright{left:46px;top:1177px;font-size:8px;color:#aaa}
.social{right:46px;top:1175px;display:flex;gap:10px}
.social i{width:11px;height:11px;border-radius:50%;background:#ddd}
</style>
</head>
<body>

<header>
  <a class="abs brand" href="#"><span class="brand-dot"></span><span class="brand-name">MTG</span></a>
  <nav class="abs top-links"><a href="#">Log In</a><span>|</span><a href="#">Register</a><span>|</span><a href="#">My Account</a><span>|</span><a href="#">Checkout</a></nav>
  <nav class="abs nav">
    <a class="active" href="#">HOME</a><a href="#">PRODUCTS</a><a href="#">WHY BUY FROM US</a><a href="#">BLOG</a><a href="#">CONTACT US</a>
  </nav>
  <a class="abs cart" href="#"><svg width="9" height="8" viewBox="0 0 9 8"><path d="M0 0h2l1 5h5l1-4H3" fill="none" stroke="#8dc21f" stroke-width="1.3"/><circle cx="3.5" cy="7" r="1" fill="#8dc21f"/><circle cx="7" cy="7" r="1" fill="#8dc21f"/></svg>MY CART <b>(0)</b></a>
  <svg class="abs search" width="8" height="8" viewBox="0 0 8 8"><circle cx="3.2" cy="3.2" r="2.4" fill="none" stroke="#333" stroke-width="1.3"/><path d="M5 5l2.5 2.5" stroke="#333" stroke-width="1.4"/></svg>
</header>

<section>
  <div class="abs hero"></div>
  <div class="abs hero-photo" role="img" aria-label="Smiling baby wearing a blue silicone bib, with orange and blue funny-face bibs"></div>
  <h1 class="abs hero-title">WE SELL BABY BIBS</h1>
  <p class="abs hero-sub">Vestibulum ante ipsum primis in faucibus orci<br>luctus et ultrices posuere cubilia</p>
  <a class="abs btn shop" href="#">SHOP NOW</a>
  <div class="abs dots"><i></i><i></i><i></i><i></i></div>
</section>

<section>
  <h2 class="abs section-title">FEATURED PRODUCTS</h2>
  <article class="abs card" style="left:46px"><div class="card-img" role="img" aria-label="Green silicone bib with funny face" style="background:linear-gradient(#8fcf3a,#5fa31e)"></div><div class="card-name">Product Name</div><div class="card-desc">Ut wisi enim ad minim veniam</div><div class="card-price">$0.00</div></article>
  <article class="abs card" style="left:210px"><div class="card-img" role="img" aria-label="Yellow silicone bib with funny face" style="background:linear-gradient(#f3ec3a,#d6cc12)"></div><div class="card-name">Product Name</div><div class="card-desc">Ut wisi enim ad minim veniam</div><div class="card-price">$0.00</div></article>
  <article class="abs card" style="left:377px"><div class="card-img" role="img" aria-label="Orange silicone bib with funny face" style="background:linear-gradient(#ffaa2a,#f08a10)"></div><div class="card-name">Product Name</div><div class="card-desc">Ut wisi enim ad minim veniam</div><div class="card-price">$0.00</div></article>
  <article class="abs card" style="left:543px"><div class="card-img" role="img" aria-label="Blue silicone bib with funny face" style="background:linear-gradient(#3aa6f0,#1677d2)"></div><div class="card-name">Product Name</div><div class="card-desc">Ut wisi enim ad minim veniam</div><div class="card-price">$0.00</div></article>
  <a class="abs cart-btn" href="#" style="left:104px"><svg width="10" height="9" viewBox="0 0 9 8"><path d="M0 0h2l1 5h5l1-4H3z" fill="#fff"/><circle cx="3.5" cy="7" r="1" fill="#fff"/><circle cx="7" cy="7" r="1" fill="#fff"/></svg></a>
  <a class="abs cart-btn" href="#" style="left:268px"><svg width="10" height="9" viewBox="0 0 9 8"><path d="M0 0h2l1 5h5l1-4H3z" fill="#fff"/><circle cx="3.5" cy="7" r="1" fill="#fff"/><circle cx="7" cy="7" r="1" fill="#fff"/></svg></a>
  <a class="abs cart-btn" href="#" style="left:435px"><svg width="10" height="9" viewBox="0 0 9 8"><path d="M0 0h2l1 5h5l1-4H3z" fill="#fff"/><circle cx="3.5" cy="7" r="1" fill="#fff"/><circle cx="7" cy="7" r="1" fill="#fff"/></svg></a>
  <a class="abs cart-btn" href="#" style="left:601px"><svg width="10" height="9" viewBox="0 0 9 8"><path d="M0 0h2l1 5h5l1-4H3z" fill="#fff"/><circle cx="3.5" cy="7" r="1" fill="#fff"/><circle cx="7" cy="7" r="1" fill="#fff"/></svg></a>
  <div class="abs divider"></div>
</section>

<section>
  <div class="abs welcome">
    <h2 class="panel-title">WELCOME !</h2>
    <p>Suspendisse lobortis turpis in odio blandit ac interdum lorem euismod. Etiam risus massa, vulputate eu pellentesque et, consectetur a neque. Aenean a nibh eget turpis vehicula tempus ac sed massa.</p>
    <a class="btn small-btn" href="#">READ MORE</a>
  </div>
  <div class="abs why">
    <h2 class="panel-title">WHY BUY FROM US</h2>
    <p>Suspendisse lobortis turpis in odio blandit ac interdum lorem euismod.<br>Etiam risus massa, vulputate eu pellentesque et..</p>
    <div class="features">
      <span><svg width="8" height="8" viewBox="0 0 8 8"><circle cx="4" cy="4" r="4" fill="#8dc21f"/><path d="M2 4l1.5 1.5L6 2.8" stroke="#fff" stroke-width="1.1" fill="none"/></svg>100% Silicon</span>
      <span><svg width="8" height="8" viewBox="0 0 8 8"><circle cx="4" cy="4" r="4" fill="#8dc21f"/><path d="M2 4l1.5 1.5L6 2.8" stroke="#fff" stroke-width="1.1" fill="none"/></svg>Soft &amp; Flexible</span>
      <span><svg width="8" height="8" viewBox="0 0 8 8"><circle cx="4" cy="4" r="4" fill="#8dc21f"/><path d="M2 4l1.5 1.5L6 2.8" stroke="#fff" stroke-width="1.1" fill="none"/></svg>They are safe</span>
      <span><svg width="8" height="8" viewBox="0 0 8 8"><circle cx="4" cy="4" r="4" fill="#8dc21f"/><path d="M2 4l1.5 1.5L6 2.8" stroke="#fff" stroke-width="1.1" fill="none"/></svg>Dishwasher safe</span>
      <span><svg width="8" height="8" viewBox="0 0 8 8"><circle cx="4" cy="4" r="4" fill="#8dc21f"/><path d="M2 4l1.5 1.5L6 2.8" stroke="#fff" stroke-width="1.1" fill="none"/></svg>Light weight</span>
      <span><svg width="8" height="8" viewBox="0 0 8 8"><circle cx="4" cy="4" r="4" fill="#8dc21f"/><path d="M2 4l1.5 1.5L6 2.8" stroke="#fff" stroke-width="1.1" fill="none"/></svg>Funny Faces</span>
    </div>
    <a class="btn small-btn" href="#">READ MORE</a>
  </div>
  <div class="abs why-img" role="img" aria-label="Pink silicone bib with funny face"></div>

  <div class="abs blog">
    <h2 class="panel-title">BLOG POSTS</h2>
    <svg class="blog-arrows" width="20" height="10" viewBox="0 0 20 10"><path d="M5 1L1 5l4 4M15 1l4 4-4 4" fill="none" stroke="#444" stroke-width="1.5"/></svg>
    <h3>Suspendisse lobortis turpis in odio blandit ac interdum lorem euismod.</h3>
    <p>Etiam risus massa, vulputate eu pellentesque et. Vestibulum vel metus sit amet turpis bibendum tincidunt vel sit amet quam...</p>
    <small>Posted on 2hrs ago</small>
  </div>
  <div class="abs news">
    <h2 class="panel-title">NEWSLETTER SIGN UP</h2>
    <p>Suspendisse lobortis turpis in odio blandit ac interdum lorem</p>
    <form class="news-form"><div class="news-input">Enter Email Address</div><div class="news-go">GO</div></form>
  </div>
</section>

<footer>
  <div class="abs footer"></div>
  <div class="abs foot-brand"><span class="brand-dot"></span><span class="brand-name">MTG</span></div>
  <p class="abs foot-about">Suspendisse lobortis turpis in odio blandit ac interdum lorem euismod. Etiam risus massa, vulputate eu...</p>
  <div class="abs foot-col" style="left:278px"><h4>QUICK LINKS</h4>Home<br>Products<br>Why buy from us<br>Blog<br>Contact us</div>
  <div class="abs foot-col" style="left:409px"><h4>MY ACCOUNT</h4>Duis aliqua<br>Nibh a dui iaculis<br>Viverra<br>Velit</div>
  <div class="abs foot-col" style="left:535px"><h4>CONTACT INFORMATIONS</h4><strong>Moon Tot Goods</strong><br>Elm Hollow, NY 00000
    <div class="contact-row"><svg width="8" height="8" viewBox="0 0 8 8"><path d="M1 0h2l1 2-1 1c.5 1 1 1.5 2 2l1-1 2 1v2C4 8 0 4 1 0z" fill="#ddd"/></svg>(555) 014-TOTS</div>
    <div class="contact-row"><svg width="9" height="7" viewBox="0 0 9 7"><rect width="9" height="7" fill="#ddd"/><path d="M0 0l4.5 4L9 0" stroke="#555" fill="none"/></svg>MoonTotGoods@mailbox-example.com</div>
  </div>
  <div class="abs foot-bar"></div>
  <p class="abs copyright">Copyright © 2016. Company Name.All Right Reserved</p>
  <div class="abs social"><i></i><i></i><i></i><i></i></div>
</footer>

</body>
</html>
```